Very dated, simple professional product website needs updating/reskinning of template

Our client currently has a very simple website at www.brightpitch4homes.example that is very, very dated, uses flash, and the template needs to have an updated look for 2014. It needs to look professional, corporate, strong colors, and if using images, actors must have a very well dressed look, etc. Client likes the layout (but not necessarily the colors, etc.) of another similar product site, www.deedcraftkit.example, for example.

The Keystoner product is an online "presentation document builder" that uses up-to-date content for agents to create 20 - 40 page presentations for potential clients. Real estate agents pay $500+ one-time plus $85/year to use the service, so the website look needs to be consistent with a $500+ product. All of the content will stay essentially the same for now: the goal is to simply re-skin the site to make it look modern, ideally through the use of new CSS files and images, and maybe some script. But we do not want to recode the whole thing, just update the template.

The site layout also needs to work with mobile devices, and so the flash has to be removed, but there is still a need to have possibly a slideshow or something to quickly grab the attention of people who visit the site so they can very quickly understand what the product is.

Also, the plan is to cut down on some of the menu buttons and/or rename them to be more compelling. There are pages on the site that can only be viewed after logging in, and we will want to use the template for those secure pages also.

Project Deadline Extended
Reason: My clients have requested that we see if we can get a few more designs to choose between, and to provide them with some time to mull over the current designs.

Project Deadline Extended
Reason: My client has requested that we continue to seek designs.

Industry/Entity Type

Product

```html
<!DOCTYPE html>
<html lang="en">
<head>
<meta charset="utf-8">
<title>Keystoner – Presentation Builder for Real Estate Agents</title>
<link href="https://fonts.googleapis.com/css2?family=Open+Sans:wght@400;600;700&family=Roboto+Condensed:wght@400;700&family=Ubuntu:wght@400;500;700&display=swap" rel="stylesheet">
<style>
:root{
  --ink-dark:#1e1e1e;
  --ink-darker:#161616;
  --footer-bg:#2b2b2b;
  --page-bg:#e6e6e6;
  --panel:#ffffff;
  --gold:#c8960f;
  --gold-bright:#d9a614;
  --orange:#e86a00;
  --green:#5a8a16;
  --text:#3a3a3a;
  --rule:#444;
  --slate:#5d6a78;
}
*{margin:0;padding:0;box-sizing:border-box}
html,body{width:960px;height:1200px;overflow:hidden}
body{position:relative;background:var(--page-bg);font-family:'Open Sans',sans-serif;color:var(--text)}
.abs{position:absolute}
.top-band{left:0;top:0;width:960px;height:338px;background:radial-gradient(circle at 190px 50px,#555 0,#2c2c2c 160px,var(--ink-dark) 320px)}
.brand{left:94px;top:28px;font-family:'Ubuntu',sans-serif;font-weight:700;font-size:40px;color:#fff;letter-spacing:1px}
.newsletter-rule{left:636px;top:32px;width:1px;height:70px;background:#3c3c3c}
.newsletter-title{left:654px;top:34px;font-family:'Ubuntu',sans-serif;font-weight:700;font-size:17px;color:#e8e8e8;letter-spacing:.5px}
.newsletter-field{left:653px;top:65px;width:155px;height:25px;background:#f4f4f4;border:1px solid #bbb;border-radius:2px 0 0 2px;font-size:10.5px;color:#888;padding:5px 8px}
.newsletter-go{left:808px;top:65px;width:30px;height:25px;background:var(--gold-bright);border-radius:0 2px 2px 0}
.nav{left:88px;top:123px;width:792px;height:32px;border-bottom:3px solid var(--gold);font-family:'Roboto Condensed',sans-serif;font-size:13px;color:#fff}
.nav a{position:absolute;top:7px;color:#fff;text-decoration:none;white-space:nowrap}
.nav .active{left:0;top:0;width:118px;height:29px;background:var(--gold);padding:7px 0 0 6px;border-radius:3px 3px 0 0;font-size:12px;letter-spacing:-.2px}
.nav .active:after{content:"";position:absolute;left:54px;bottom:0;border:5px solid transparent;border-bottom-color:#fff;border-top:0}
.hero{left:82px;top:166px;width:796px;height:355px;border:3px solid #fff;border-radius:4px;background:linear-gradient(180deg,#a9c3d8 0%,#d9dee0 35%,#c7b9a1 60%,#6d5b3a 85%,#3d3524 100%);box-shadow:0 2px 6px rgba(0,0,0,.3)}
.caption{left:99px;top:218px;width:228px;height:228px;background:rgba(38,38,40,.88);border-radius:4px;padding:16px 14px}
.caption h1{font-weight:400;font-size:17px;line-height:23px;color:#fff;letter-spacing:.3px}
.caption h1 span{display:block;color:var(--gold-bright);font-weight:600}
.caption p{margin-top:14px;font-size:10.8px;line-height:19px;color:#eee}
.arrow{top:390px;width:31px;height:30px}
.arrow.prev{left:115px;background:#a88a1e}
.arrow.next{left:146px;background:var(--slate)}
.features{left:82px;top:550px;width:796px;height:308px;background:var(--panel);border-radius:4px}
.feature{position:absolute;top:14px;width:248px}
.feature h2{font-family:'Ubuntu',sans-serif;font-weight:700;font-size:19px;color:var(--gold);height:34px}
.feature .photo{width:222px;height:74px;border:1px solid #bbb}
.feature .lead{margin-top:14px;font-size:9.3px;font-weight:700;line-height:14px;color:#333}
.feature ul{list-style:none;margin-top:10px}
.feature li{font-size:10px;line-height:17px;padding-left:9px;position:relative;color:#333}
.feature li:before{content:"›";position:absolute;left:0;top:0;font-weight:700}
.more{position:absolute;left:2px;top:262px;width:245px;border-top:1px solid #ddd}
.more span{position:absolute;right:24px;top:-7px;background:#fff;padding:0 4px;font-size:9px;font-weight:700}
.more.orange span{color:var(--orange)}
.more.green span{color:var(--green)}
.footer-area{left:0;top:877px;width:960px;height:289px;background:var(--footer-bg)}
.footer-area h3{position:absolute;font-family:'Roboto Condensed',sans-serif;font-weight:400;font-size:19px;color:#f0f0f0}
.rule-h{position:absolute;height:1px;background:var(--rule)}
.rule-v{position:absolute;width:1px;background:var(--rule)}
.quote{left:98px;top:65px;width:152px;font-size:9.6px;line-height:16.8px;color:#e4e4e4;text-indent:30px}
.qmark{font-family:Georgia,serif;font-size:40px;color:#666;position:absolute;line-height:1}
.qmark-end{font-family:Georgia,serif;font-size:30px;color:#666;line-height:0;vertical-align:-10px;margin-left:4px}
.map-text{left:296px;top:58px;width:340px;font-size:10.4px;line-height:18px;color:#ddd}
.map{left:306px;top:100px;width:312px;height:163px;background:linear-gradient(135deg,#ece8dc,#e3dfd2 50%,#eee9da);border:1px solid #555}
.field{position:absolute;left:674px;width:172px;height:19px;border:1px solid #555;background:#303030;font-size:9.6px;color:#ccc;padding:2px 7px}
.submit{left:799px;top:165px;width:47px;height:19px;background:var(--orange);border-radius:2px;color:#fff;font-family:'Ubuntu',sans-serif;font-weight:700;font-size:10px;text-align:center;line-height:19px}
.address{left:665px;top:201px;font-size:8.8px;line-height:14.5px;color:#f2f2f2;font-weight:600}
.address b{color:#29a8e0}
.world{left:772px;top:199px;width:72px;height:34px;background:radial-gradient(ellipse at center,#777 0,#555 60%,transparent 72%)}
.bottom-bar{left:0;top:1166px;width:960px;height:34px;background:var(--ink-darker);font-family:'Roboto Condensed',sans-serif;font-size:11.2px;color:#eee;padding:9px 0 0 86px}
.bottom-bar a{color:#eee;text-decoration:none}
.bottom-bar i{font-style:normal;margin:0 11px}
.social{top:1174px;width:16px;height:16px;border-radius:2px}
</style>
</head>
<body>
<div class="abs top-band"></div>
<div class="abs brand">Keystoner</div>

<div class="abs newsletter-rule"></div>
<h2 class="abs newsletter-title">Subscribe Newsletter</h2>
<div class="abs newsletter-field">Email Address</div>
<div class="abs newsletter-go">
  <svg width="30" height="25" viewBox="0 0 30 25"><circle cx="13" cy="11" r="6" fill="none" stroke="#fff" stroke-width="1.6"/><line x1="17" y1="15" x2="22" y2="20" stroke="#fff" stroke-width="2"/></svg>
</div>

<nav class="abs nav">
  <a class="active">Getting The Business</a>
  <a style="left:155px">What is Keystoner</a>
  <a style="left:277px">Peer Reviews</a>
  <a style="left:380px">FAQ</a>
  <a style="left:439px">About Us</a>
</nav>

<div class="abs hero" role="img" aria-label="Photo of a two-storey suburban house at dusk with warm lit windows"></div>
<div class="abs caption">
  <h1>Where Great <span>Presentation Begin</span></h1>
  <p>Typesetting industry. Lorem Ipsum has been the industry's standard dummy text ever since the 1500s, when an unknown.</p>
</div>
<div class="abs arrow prev"><svg width="31" height="30"><polyline points="18,9 12,15 18,21" fill="none" stroke="#fff" stroke-width="1.5"/></svg></div>
<div class="abs arrow next"><svg width="31" height="30"><polyline points="13,9 19,15 13,21" fill="none" stroke="#fff" stroke-width="1.5"/></svg></div>

<section class="abs features">
  <div class="feature" style="left:20px">
    <h2>WHAT IS KEYSTONER</h2>
    <div class="photo" role="img" aria-label="Photo of brick family homes on a green lawn" style="background:linear-gradient(180deg,#8fb2d6,#b07a5c 55%,#5d7a3a)"></div>
    <p class="lead">If your business needs include Lakeview IT Services, consider locally-owned Ridgeline Systems.</p>
    <ul><li>Business process &amp; system automation</li><li>Network solutions</li><li>Managed services</li><li>Data services</li><li>Staff augmentation</li></ul>
    <div class="more orange"><span>More Info</span></div>
  </div>
  <div class="feature" style="left:280px">
    <h2>KEYSTONER DEMO</h2>
    <div class="photo" role="img" aria-label="Photo of a Mediterranean villa among palm trees" style="background:linear-gradient(180deg,#7fa4cc,#c9b08a 55%,#4f5a33)"></div>
    <p class="lead">Ridgeline Systems provides full-service web design, development and hosting solutions.</p>
    <ul><li>Database programming capabilities</li><li>Browser-based email access</li><li>Content management &amp; customization</li><li>Browser-based email access</li><li>Content management &amp; customization</li></ul>
    <div class="more green"><span>More Info</span></div>
  </div>
  <div class="feature" style="left:540px">
    <h2>ORDER KEYSTONER</h2>
    <div class="photo" role="img" aria-label="Photo of a smiling buyer holding car keys in a vehicle" style="background:linear-gradient(135deg,#3c3c3c,#8a8f92 45%,#c2302a 85%)"></div>
    <p class="lead">If your business needs include Lakeview IT Services, consider locally-owned Ridgeline Systems.</p>
    <ul><li>Business process &amp; system automation</li><li>Network solutions</li><li>Managed services</li><li>Data services</li><li>Staff augmentation</li></ul>
    <div class="more green"><span>More Info</span></div>
  </div>
</section>

<footer class="abs footer-area">
  <h3 style="left:98px;top:10px">Testimonials</h3>
  <div class="rule-h" style="left:94px;top:39px;width:158px"></div>
  <span class="qmark" style="left:96px;top:58px">“</span>
  <p class="abs quote">Lorem ipsum dolor sit amet, consectetur adipiscing elit. Sed nec diam magna, a semper est. Phasellus vulputate aliquam elit vitae sagittis. Cras convallis blandit ornare. Proin eget nibh at odio ullamcorper molestie ut at mauris. Integer non orci sapien, a lobortis turpis. Nullam quis dui ligula. Morbi luctus vestibulum elit, in luctus urna cursus non.<span class="qmark-end">”</span></p>
  <div class="rule-v" style="left:274px;top:11px;height:268px"></div>

  <h3 style="left:295px;top:10px">Location Map</h3>
  <div class="rule-h" style="left:295px;top:39px;width:341px"></div>
  <p class="abs map-text">Typesetting industry. Lorem Ipsum has been the industry's standard dummy text ever since the 1500s, when an unknown</p>
  <div class="abs map" role="img" aria-label="Street map showing the office location"></div>
  <div class="rule-v" style="left:650px;top:11px;height:268px"></div>

  <h3 style="left:674px;top:14px">Contact</h3>
  <div class="rule-h" style="left:672px;top:43px;width:174px"></div>
  <div class="field" style="top:51px">Name</div>
  <div class="field" style="top:74px">Email</div>
  <div class="field" style="top:97px">Phone</div>
  <div class="field" style="top:121px;height:37px;padding-top:12px">Massege</div>
  <div class="abs submit">Submit</div>
  <div class="abs world" role="img" aria-label="Faint world map decoration"></div>
  <p class="abs address">4800 Harbor Lane #210<br>Millbrook OH 40000<br>555-010-KEYS<br><b>P:</b> 000 123 456 7890 &nbsp;/&nbsp; <b>P:</b> 000 123 456 7890</p>
</footer>

<div class="abs bottom-bar">
  <a>Home</a><i>|</i><a>Getting The Business</a><i>|</i><a>What is Keystoner</a><i>|</i><a>Peer Reviews</a><i>|</i><a>FAQ</a><i>|</i><a>About Us</a>
</div>
<div class="abs social" style="left:787px;background:#3b5a98"></div>
<div class="abs social" style="left:808px;background:#1d7bb8"></div>
<div class="abs social" style="left:830px;background:#33b3e6"></div>
<div class="abs social" style="left:851px;background:#f07a16"></div>
</body>
</html>
```